Website images and banners needed to be created

We have a website we have not used in a few months that need updated sales banners and images resized for our web devs to upload and update. The site in question is w w w . p a l t r o n . c o m

Number of Pages Required

3 page

```html
<!DOCTYPE html>
<html lang="en">
<head>
<meta charset="utf-8">
<title>Paltron – Black Friday Banners</title>
<link href="https://fonts.googleapis.com/css2?family=Quicksand:wght@500;600;700&family=Mulish:wght@400;600&display=swap" rel="stylesheet">
<style>
  :root{
    --page:#fdf8e7;
    --accent:#fcc800;
    --white:#ffffff;
    --footer:#141414;
    --footer-text:#e6e6e6;
    --dark-room-a:#2a2421;
    --dark-room-b:#3a302a;
    --light-room-a:#d9d6cf;
    --light-room-b:#77736c;
    --night-room-a:#2b2e33;
    --night-room-b:#4a3a2a;
  }
  *{margin:0;padding:0;box-sizing:border-box}
  html,body{width:1200px;height:2233px;overflow:hidden;background:var(--page)}
  body{position:relative;font-family:'Quicksand',sans-serif}
  .banner{position:absolute;left:67px;width:1066px;height:668px;overflow:hidden;box-shadow:0 0 0 1px rgba(0,0,0,.08)}
  .banner--one{top:46px}
  .banner--two{top:766px}
  .banner--three{top:1488px}
  .banner__photo{position:absolute;left:0;top:0;width:1066px;height:611px}
  .photo--dark{background:radial-gradient(ellipse at 50% 70%,#4a3f38 0%,var(--dark-room-a) 55%,#16120f 100%)}
  .photo--light{background:linear-gradient(100deg,var(--light-room-a) 0%,#cfcbc3 45%,#8f8b84 70%,var(--light-room-b) 100%)}
  .photo--night{background:radial-gradient(ellipse at 35% 75%,#5a4632 0%,var(--night-room-b) 30%,var(--night-room-a) 70%,#1c1e22 100%)}
  .banner__tint{position:absolute;left:0;top:0;width:1066px;height:611px}
  .brand{position:absolute;left:68px;top:28px;display:flex;align-items:center;gap:18px;color:var(--white);font-weight:700;font-size:40px;letter-spacing:.5px}
  .brand__mark{width:34px;height:26px;border:3px solid var(--white);border-radius:2px}
  .actions{position:absolute;top:32px;left:910px;display:flex;gap:7px}
  .actions__btn{width:41px;height:41px;border:2px solid var(--white);border-radius:50%;display:flex;align-items:center;justify-content:center}
  .offer{position:absolute;color:var(--white);font-weight:700;line-height:1}
  .offer--center{left:0;width:1066px;text-align:center}
  .offer__deal{color:var(--accent);font-size:47px;font-weight:600;white-space:nowrap}
  .offer__pct{font-size:70px;font-weight:700;margin:0 2px}
  .offer__off{font-weight:700}
  .offer__title{font-size:45px;font-weight:600;margin-top:8px;white-space:nowrap}
  .offer__title--big{font-size:50px;margin-top:14px}
  .offer__title--sub{font-size:40px;margin-top:16px}
  .shop-btn{display:inline-block;background:var(--accent);color:var(--white);font-weight:600;font-size:19px;width:158px;height:49px;line-height:49px;border-radius:25px;text-align:center}
  .offer--center .shop-btn{margin-top:22px}
  .offer--left{left:65px;top:262px}
  .offer--left .shop-btn{margin-top:32px;margin-left:2px}
  .footer{position:absolute;left:0;top:611px;width:1066px;height:57px;background:var(--footer)}
  .footer__copy{position:absolute;left:66px;top:21px;font-family:'Mulish',sans-serif;font-size:10.5px;color:var(--footer-text)}
  .footer__social{position:absolute;left:836px;top:14px;display:flex;gap:4px}
  .footer__dot{width:29px;height:29px;border:1.5px solid var(--white);border-radius:50%}
</style>
</head>
<body>

<section class="banner banner--one">
  <div class="banner__photo photo--dark" role="img" aria-label="Dark bedroom with a low bed, pendant lamps and side tables"></div>
  <div class="banner__tint" style="background:rgba(0,0,0,.25)"></div>
  <div class="brand"><span class="brand__mark"></span>paltron.com</div>
  <div class="actions">
    <span class="actions__btn"><svg width="18" height="16" viewBox="0 0 18 16"><path d="M1 5h16l-2 10H3z M6 5l3-4 3 4" fill="none" stroke="#fff" stroke-width="1.8" stroke-linejoin="round"/><path d="M6 8v4M9 8v4M12 8v4" stroke="#fff" stroke-width="1.4"/></svg></span>
    <span class="actions__btn"><svg width="14" height="12" viewBox="0 0 14 12"><path d="M1 2h12M1 6h12M1 10h12" stroke="#fff" stroke-width="2"/></svg></span>
  </div>
  <div class="offer offer--center" style="top:188px">
    <div class="offer__deal">Upto<span class="offer__pct">70%</span><span class="offer__off">OFF</span></div>
    <div class="offer__title">The Big Black Friday Event</div>
    <span class="shop-btn">Shop Now!</span>
  </div>
  <footer class="footer">
    <p class="footer__copy">© Copyright 2019- Paltron.All Rights Reserved</p>
    <div class="footer__social"><span class="footer__dot"></span><span class="footer__dot"></span><span class="footer__dot"></span><span class="footer__dot"></span><span class="footer__dot"></span></div>
  </footer>
</section>

<section class="banner banner--two">
  <div class="banner__photo photo--light" role="img" aria-label="Bright bedroom with a tufted headboard, grey bedding, mirror and framed prints"></div>
  <svg class="banner__tint" viewBox="0 0 1066 611" aria-hidden="true"><polygon points="0,0 310,0 560,611 0,611" fill="#c9c08a" opacity=".75"/></svg>
  <div class="brand"><span class="brand__mark"></span>paltron.com</div>
  <div class="actions">
    <span class="actions__btn"><svg width="18" height="16" viewBox="0 0 18 16"><path d="M1 5h16l-2 10H3z M6 5l3-4 3 4" fill="none" stroke="#fff" stroke-width="1.8" stroke-linejoin="round"/><path d="M6 8v4M9 8v4M12 8v4" stroke="#fff" stroke-width="1.4"/></svg></span>
    <span class="actions__btn"><svg width="14" height="12" viewBox="0 0 14 12"><path d="M1 2h12M1 6h12M1 10h12" stroke="#fff" stroke-width="2"/></svg></span>
  </div>
  <div class="offer offer--left">
    <div class="offer__deal">Upto<span class="offer__pct">70%</span><span class="offer__off">OFF</span></div>
    <div class="offer__title offer__title--big">The Big Black</div>
    <div class="offer__title offer__title--sub">Friday Event</div>
    <span class="shop-btn">Shop Now!</span>
  </div>
  <footer class="footer">
    <p class="footer__copy">© Copyright 2019- Paltron.All Rights Reserved</p>
    <div class="footer__social"><span class="footer__dot"></span><span class="footer__dot"></span><span class="footer__dot"></span><span class="footer__dot"></span><span class="footer__dot"></span></div>
  </footer>
</section>

<section class="banner banner--three">
  <div class="banner__photo photo--night" role="img" aria-label="Evening bedroom with a knitted throw on the bed and a tall wooden floor lamp"></div>
  <div class="banner__tint" style="background:rgba(0,0,0,.2)"></div>
  <div class="brand"><span class="brand__mark"></span>paltron.com</div>
  <div class="actions">
    <span class="actions__btn"><svg width="18" height="16" viewBox="0 0 18 16"><path d="M1 5h16l-2 10H3z M6 5l3-4 3 4" fill="none" stroke="#fff" stroke-width="1.8" stroke-linejoin="round"/><path d="M6 8v4M9 8v4M12 8v4" stroke="#fff" stroke-width="1.4"/></svg></span>
    <span class="actions__btn"><svg width="14" height="12" viewBox="0 0 14 12"><path d="M1 2h12M1 6h12M1 10h12" stroke="#fff" stroke-width="2"/></svg></span>
  </div>
  <div class="offer offer--center" style="top:240px">
    <div class="offer__deal">Upto<span class="offer__pct">70%</span><span class="offer__off">OFF</span></div>
    <div class="offer__title">The Big Black Friday Event</div>
    <span class="shop-btn">Shop Now!</span>
  </div>
  <footer class="footer">
    <p class="footer__copy">© Copyright 2019- Paltron.All Rights Reserved</p>
    <div class="footer__social"><span class="footer__dot"></span><span class="footer__dot"></span><span class="footer__dot"></span><span class="footer__dot"></span><span class="footer__dot"></span></div>
  </footer>
</section>

</body>
</html>
```